BUSINESS CARD DESIGN

NAME- DALE VORSKIN
PHONE NUMER - 555- 714-9082
EMAIL- OFFICE@TRV-GROUNDMAKRZ.COM
BACK OF CARD- SPEACIALIZES IN LAND CLEARING, FORESTRY MUCLHING AND EXCAVATION

Contact Information for Business Card

NAME- DALE VORSKIN PHONE NUMER - 555- 714-9082 EMAIL- OFFICE@TRV-GROUNDMAKRZ.COM BACK OF CARD- SPEACIALIZES IN LAND CLEARING , MUCLHING AND EXCAVATION

```html
<!DOCTYPE html>
<html lang="en">
<head>
<meta charset="utf-8">
<title>Business Card — Dale Vorskin</title>
<link href="https://fonts.googleapis.com/css2?family=Montserrat:wght@400;500;700&display=swap" rel="stylesheet">
<style>
  :root {
    --backdrop: #e9e5df;
    --card-white: #ffffff;
    --card-black: #060606;
    --gold: #f6b21b;
    --ink: #1d1d1d;
    --faint: #d4d4d4;
  }
  * { margin: 0; padding: 0; box-sizing: border-box; }
  html, body {
    width: 900px; height: 1200px; overflow: hidden;
    background: var(--backdrop);
    font-family: "Montserrat", sans-serif;
  }
  .canvas { position: relative; width: 900px; height: 1200px; }
  .card {
    position: absolute; left: 80px; width: 742px; height: 440px;
    border-radius: 22px; overflow: hidden;
  }
  .card-front { top: 131px; background: var(--card-white); }
  .card-back { top: 638px; background: var(--card-black); }

  .brand {
    position: absolute; display: flex; flex-direction: column; align-items: center;
    font-weight: 700; letter-spacing: 1px; text-transform: uppercase; text-align: center;
  }
  .brand-dot { border-radius: 50%; flex: none; }

  .front-brand { left: 40px; width: 260px; top: 24px; gap: 14px; color: var(--ink); font-size: 19px; line-height: 1.25; }
  .front-brand .brand-dot { width: 112px; height: 112px; background: var(--ink); }

  .watermark-brand { left: 400px; width: 330px; top: 150px; gap: 14px; color: var(--faint); font-size: 22px; line-height: 1.2; }
  .watermark-brand .brand-dot { width: 200px; height: 200px; background: var(--faint); }

  .person { position: absolute; right: 32px; top: 40px; text-align: right; }
  .person-name { color: var(--gold); font-weight: 700; font-size: 25px; letter-spacing: 0.3px; }
  .person-role { color: var(--ink); font-size: 16px; font-weight: 500; margin-top: 2px; }

  .contacts { position: absolute; left: 43px; top: 322px; list-style: none; }
  .contacts li {
    display: flex; align-items: center; gap: 8px; height: 28px;
    color: var(--ink); font-size: 16px; font-weight: 500;
  }
  .contacts svg { width: 16px; height: 16px; fill: var(--gold); flex: none; }

  .back-brand { left: 0; right: 0; top: 62px; gap: 22px; color: var(--gold); font-size: 30px; }
  .back-brand .brand-dot { width: 170px; height: 170px; background: var(--gold); }

  .specialty {
    position: absolute; left: 60px; right: 60px; top: 330px;
    color: var(--gold); font-size: 14px; font-weight: 500; letter-spacing: 2px;
    text-align: center; text-transform: uppercase; line-height: 1.5;
  }
</style>
</head>
<body>
<main class="canvas">
  <section class="card card-front">
    <div class="brand front-brand"><span class="brand-dot"></span><span>Trevian<br>Groundmakrz LLC</span></div>
    <div class="brand watermark-brand" aria-hidden="true"><span class="brand-dot"></span><span>Trevian Groundmakrz</span></div>
    <div class="person">
      <p class="person-name">DALE VORSKIN</p>
      <p class="person-role">Managing Director</p>
    </div>
    <ul class="contacts">
      <li><svg viewBox="0 0 24 24"><path d="M6.6 10.8a15 15 0 0 0 6.6 6.6l2.2-2.2c.3-.3.7-.4 1-.2 1.1.4 2.3.6 3.6.6.6 0 1 .4 1 1V20c0 .6-.4 1-1 1A17 17 0 0 1 3 4c0-.6.4-1 1-1h3.5c.6 0 1 .4 1 1 0 1.3.2 2.5.6 3.6.1.3 0 .7-.2 1z"/></svg>555- 714-9082</li>
      <li><svg viewBox="0 0 24 24"><path d="M2 5h20v2l-10 6L2 7zM2 9.3l10 6 10-6V19H2z"/></svg>OFFICE@TRV-GROUNDMAKRZ.COM</li>
      <li><svg viewBox="0 0 24 24"><path d="M12 2a10 10 0 1 0 0 20 10 10 0 0 0 0-20zm6.9 6h-3a15 15 0 0 0-1.3-3.9A8 8 0 0 1 18.9 8zM12 4c.8 1.2 1.5 2.5 1.9 4h-3.8c.4-1.5 1.1-2.8 1.9-4zM4.3 14a8 8 0 0 1 0-4h3.4a16 16 0 0 0 0 4zm.8 2h3a15 15 0 0 0 1.3 3.9A8 8 0 0 1 5.1 16zm3-8h-3a8 8 0 0 1 4.3-3.9C8.8 5.3 8.4 6.6 8.1 8zM12 20c-.8-1.2-1.5-2.5-1.9-4h3.8c-.4 1.5-1.1 2.8-1.9 4zm2.3-6H9.7a14 14 0 0 1 0-4h4.6a14 14 0 0 1 0 4zm.3 5.9c.6-1.2 1-2.5 1.3-3.9h3a8 8 0 0 1-4.3 3.9zm1.7-5.9a16 16 0 0 0 0-4h3.4a8 8 0 0 1 0 4z"/></svg>WWW.TRV-GROUNDMAKRZ.COM</li>
    </ul>
  </section>

  <section class="card card-back">
    <div class="brand back-brand"><span class="brand-dot"></span><span>Trevian Groundmakrz LLC</span></div>
    <p class="specialty">Specializes in land clearing,<br>forestry mulching and excavation</p>
  </section>
</main>
</body>
</html>
```